Poster for a Bicycle show/Expo

We need a poster for a Bicycle show/Expo and sustainable transport. Exhibitors will sell bikes, cycling clothing, accessories, etc. ...
This show is annual and the Poster is for the 2015 edition.

The style must be modern, dynamic, bright colors.

Your concept must be compatible in a landscape format. (We will ourselves adaptations of different formats.)
Width: 210 mm
Height: 297 mm
It's necessary for us to have the source file (vector) for make, later, the different format (flyers, website, ...)

Content of the Poster:
- 1 big picture (no clip art)
- Big title: « Foire du Rayon » (« Salon » or « Salon du » can be small and « Vélo » big.)
- Subtitle: « et de la mobilité douce »
- Date: « 8, 9 et 10 mai 2015 » or « 8-10 mai 2015 »
- Place: « Halle TRV - Gare de Lunel »
- Text line 1: « www.foire-du-rayon.ch - Entrée gratuite »
- Text line 2« Piste d’essais - Restauration sur place »
- Text line 3: « Ve 8 mai de 17h à 21h - Sa 9 mai de 10h à 20h - Di 10 mai de 10h à 18h »
- Please, leave a zone in the poster for sponsors logos
(The predominant information (most visible) are: « Foire du Rayon » and « 8, 9 et 10 mai 2015 or 8-10 mai 2015 »)

Content of the big picture:
- from a cheap stock, like PixKiosk.com
- a bicycle in action or a detail of a bicycle (or a accessory) (no race bike)
- a modern picture with bright colors.
- if a person is on the picture, we prefer a men
- not an aerial view with cyclists in a landscape.

Some examples of poster of shows - with typo-title worked

http://www.expobassinlutece.com/Temp/IMG/F_a9b3c2d4e5f60718293a4b5c6d7e8f9012345678901_200_296.png

http://qx4m.tornafoire.fr/Data/pvtorn_mer/block/F_7cc1bb9396aef1d5e69283647561f0076457c357c5ea6.pdf
(page 2 of this PDF)

http://salons.rivol-evenements.fr/images/rivol-evenements/foires-salons/phototheque/salon-auto-bourlac/salon-auto-bourlac2012-affiche.jpg

http://www.tirovel.net/blog/wp-content/uploads/2007/03/affiche-salon-du-livre.jpg

http://www.quaimarin-gens.com/wp-content/affiche-cannes-2007.jpg
Updates

Hello,

For information, for your next versions, please, add the text "Piste d'essais".

- Text line 1: « www.foire-du-rayon.ch - Entrée gratuite »
- Text line 2: « Piste d’essais - Restauration sur place »
- Text line 3: « Ve 8 mai de 17h à 21h - Sa 9 mai de 10h à 20h - Di 10 mai de 10h à 18h »

Thanks,
Rodolphe

```html
<!DOCTYPE html>
<html lang="fr">
<head>
<meta charset="utf-8">
<title>Foire du Rayon et de la mobilité douce – 8-10 mai 2015</title>
<link rel="stylesheet" href="https://fonts.googleapis.com/css2?family=Bebas+Neue&display=swap">
<style>
  :root {
    --backdrop: #e4e4e4;
    --paper: #ffffff;
    --ink: #121212;
    --teal: #4db3c0;
    --green: #8cc43c;
    --band: #333333;
    --band-text: #ffffff;
    --sky-top: #5f9fd6;
    --sky-low: #c9dff0;
    --earth: #b39a78;
    --ground: #6f6a63;
  }
  * { margin: 0; padding: 0; box-sizing: border-box; }
  html, body {
    width: 1200px;
    height: 1152px;
    overflow: hidden;
    background: var(--backdrop);
  }
  body { position: relative; font-family: "Bebas Neue", "Arial Narrow", sans-serif; }

  .poster {
    position: absolute;
    left: 218px;
    top: 36px;
    width: 764px;
    height: 1080px;
    background: var(--paper);
    overflow: hidden;
  }

  .title-small {
    position: absolute;
    left: 50px;
    top: 24px;
    font-size: 90px;
    line-height: 1;
    color: var(--ink);
    white-space: nowrap;
  }
  .title-big {
    position: absolute;
    left: 46px;
    top: 115px;
    font-size: 196px;
    line-height: 1;
    color: var(--ink);
    white-space: nowrap;
  }
  .test-track {
    position: absolute;
    left: 428px;
    top: 282px;
    transform: rotate(-90deg);
    transform-origin: left top;
    font-size: 36px;
    line-height: 1;
    color: var(--ink);
    white-space: nowrap;
  }
  .event-info {
    position: absolute;
    left: 470px;
    top: 196px;
    color: var(--teal);
  }
  .event-date { font-size: 60px; line-height: 1; white-space: nowrap; }
  .event-place { font-size: 25px; line-height: 1; margin-top: 6px; white-space: nowrap; }

  .subtitle {
    position: absolute;
    left: 50px;
    top: 298px;
    font-size: 84px;
    line-height: 1;
    color: var(--green);
    white-space: nowrap;
  }

  .hero-photo {
    position: absolute;
    left: 0;
    top: 382px;
    width: 764px;
    height: 535px;
    background:
      linear-gradient(180deg, var(--sky-top) 0%, var(--sky-low) 45%, var(--earth) 68%, var(--ground) 100%);
  }

  .info-band {
    position: absolute;
    left: 0;
    top: 926px;
    width: 764px;
    height: 56px;
    background: var(--band);
    color: var(--band-text);
    text-align: center;
  }
  .info-main { font-size: 24px; line-height: 1; padding-top: 8px; letter-spacing: 0.2px; white-space: nowrap; }
  .info-hours {
    display: flex;
    justify-content: center;
    gap: 40px;
    font-size: 14px;
    line-height: 1;
    margin-top: 6px;
    color: var(--teal);
    white-space: nowrap;
  }
  .info-hours span + span::before { content: "•"; margin-right: 40px; color: var(--band-text); }

  .sponsors {
    position: absolute;
    left: 0;
    top: 992px;
    width: 764px;
    height: 76px;
    display: flex;
    justify-content: space-around;
    align-items: center;
    padding: 0 40px;
  }
  .sponsor {
    display: flex;
    align-items: center;
    gap: 8px;
    font-size: 30px;
    line-height: 1;
    color: var(--ink);
  }
  .sponsor-square { width: 14px; height: 14px; background: var(--ink); }
  .sponsor-circle { width: 14px; height: 14px; border-radius: 50%; background: var(--ink); }
</style>
</head>
<body>
  <main class="poster">
    <h1>
      <span class="title-small">Foire du</span>
      <span class="title-big">Rayon</span>
    </h1>
    <p class="test-track">Piste d'essais</p>
    <div class="event-info">
      <p class="event-date">8-10 mai 2015</p>
      <p class="event-place">Halle TRV - Gare de Lunel</p>
    </div>
    <h2 class="subtitle">Et de la mobilité douce</h2>

    <div class="hero-photo" role="img" aria-label="Photo en contre-plongée d'un cycliste en VTT blanc sur un chemin de terre, roue arrière en gros plan, ciel bleu et végétation sèche"></div>

    <section class="info-band">
      <p class="info-main">www.foire-du-rayon.ch - Entrée gratuite - Restauration sur place</p>
      <p class="info-hours">
        <span>Ve 8 mai de 17h à 21h</span>
        <span>Sa 9 mai de 10h à 20h</span>
        <span>Di 10 mai de 10h à 18h</span>
      </p>
    </section>

    <footer class="sponsors">
      <div class="sponsor"><span class="sponsor-square"></span>Veltra</div>
      <div class="sponsor">Corsin</div>
      <div class="sponsor">Rumo</div>
      <div class="sponsor"><span class="sponsor-circle"></span>Drela</div>
    </footer>
  </main>
</body>
</html>
```